Design my site www.brieflyledger.com

So here is what I am thinking in terms of design:

https://plenvo.com

https://www.skyluxair.com

http://kalvex.com/harbor-plaza-tower/

I want the theme to be white and blue (royal blue). I attached a paint picture of what I would like the site to look like in terms of placing the text. Generally, what I like about the sites above is that they are simple, you can navigate easily and have some kind of idea of what's going on by looking at the center (picture and motto). Let's establish a clear understanding of how the functional part of the site would look like. Please see the picture attached.

I want to keep it simple: On top would be the Name 'BRIEFLY ledger", somewhere to the right on top on the page would be 'Sign in" button.

In the center would be a picture (maybe a video) with the Motto (on top of it all in capital) OBSERVE NAVIGATE DECIDE and below would be the "sign up now"

Below the picture (like on kalvex.com site) or to the left on top of the page would be "About Us', "Press" "Contact Us' buttons.

Then once the user gets to his page his got 3 tabs " Press Headlines", "Events", " Briefings".

we would keep the same format I only have on the site, but separate for every Tab.

I do not want the user to get distracted. I also want him to be able to access the page though mobile phone and be able to get automatic updates just like Zorvan Pings without having to sign in daily.

The landing page must be minimalist yet with business/corporate feel where users can navigate easily and a "what you see is what you get" approach. You want an image or video (personally I prefer the video.. it does capture the users attention instantly, as long as it is an interesting video), with your taglines in it.

Sections available to public: About Us, Contact Us, Landing Page with Signup Option

Private: Public Sections + User Account Page, Tabs for (Events, Press Headlines, Briefings)

Target Market(s)

PR/media monitoring/diplomatic community

Coding

Coded - Design and coding required

Number of Pages Required

1 page

Font styles to use
Serif
Sans Serif

Colors
0255a3
ec1f27

Requirements
Must have
• a simple landing page, that is user friendly.
Nice to have
• a video with the explanation of how to navigate the site
Should not have
• too many colors, graphs etc.

```html
<!DOCTYPE html>
<html lang="en">
<head>
<meta charset="utf-8">
<title>BRIEFLY ledger – Events</title>
<link href="https://fonts.googleapis.com/css2?family=Open+Sans:wght@400;600;700&display=swap" rel="stylesheet">
<style>
  :root {
    --brand-blue: #2e8fc2;
    --brand-blue-dark: #257fb0;
    --ink: #3a3a3a;
    --muted: #666;
    --panel-bg: #f5f5f5;
    --panel-border: #dcdcdc;
    --field-border: #d6d6d6;
    --footer-bg: #f7f7f7;
    --white: #ffffff;
  }
  * { box-sizing: border-box; margin: 0; padding: 0; }
  html, body { width: 1200px; height: 896px; overflow: hidden; }
  body {
    position: relative;
    background: var(--white);
    font-family: "Open Sans", Arial, sans-serif;
    color: var(--ink);
  }
  .hero {
    position: absolute; left: 0; top: 0; width: 1200px; height: 258px;
    background: linear-gradient(180deg, #3c4a5e 0%, #4e5b6c 35%, #3a4250 70%, #2b3039 100%);
  }
  .brand {
    position: absolute; left: 97px; top: 40px; width: 313px; height: 57px;
    background: var(--white);
    display: flex; align-items: center; justify-content: center;
    font-weight: 700; font-size: 31px; letter-spacing: 0.5px;
    color: var(--brand-blue);
  }
  .sign-in {
    position: absolute; left: 982px; top: 52px; width: 83px; height: 32px;
    background: var(--brand-blue); border: 1px solid #8cc5e3; border-radius: 3px;
    color: var(--white); font-weight: 700; font-size: 13px;
    display: flex; align-items: center; justify-content: center;
  }
  .menu-toggle { position: absolute; left: 1078px; top: 58px; }
  .tabs {
    position: absolute; left: 99px; top: 296px; width: 1001px; height: 42px;
    border-bottom: 1px solid var(--brand-blue);
    display: flex;
  }
  .tab {
    height: 41px; display: flex; align-items: center; justify-content: center;
    font-weight: 600; font-size: 15.5px; color: var(--ink);
  }
  .tab--press { width: 212px; }
  .tab--events { width: 206px; background: var(--brand-blue); color: var(--white); }
  .tab--briefings { width: 243px; }
  .search-panel {
    position: absolute; left: 97px; top: 338px; width: 1003px; height: 381px;
    background: var(--panel-bg); border: 1px solid var(--panel-border); border-top: none;
  }
  .field { position: absolute; width: 348px; }
  .field label { display: block; font-size: 13.5px; color: var(--muted); height: 19px; }
  .field .input {
    margin-top: 10px; height: 35px; background: var(--white);
    border: 1px solid var(--field-border); border-radius: 2px;
    position: relative; font-size: 11px; color: var(--muted);
    padding-left: 11px; line-height: 33px;
  }
  .field .input::after {
    content: ""; position: absolute; right: 35px; top: 0; bottom: 0;
    border-left: 1px solid #eee;
  }
  .field .caret { position: absolute; right: 12px; top: 14px; }
  .col-1 { left: 50px; } .col-2 { left: 426px; }
  .row-1 { top: 53px; } .row-2 { top: 122px; } .row-3 { top: 190px; }
  .submit {
    position: absolute; left: 51px; top: 276px; width: 127px; height: 37px;
    background: var(--brand-blue); border-radius: 2px;
    color: var(--white); font-size: 15.5px;
    display: flex; align-items: center; justify-content: center;
  }
  .site-footer {
    position: absolute; left: 0; top: 785px; width: 1200px; height: 111px;
    background: var(--footer-bg); border-top: 1px solid #ececec;
  }
  .footer-nav {
    position: absolute; left: 98px; top: 36px;
    font-size: 12.5px; font-weight: 600; color: var(--brand-blue);
  }
  .footer-nav .sep { color: var(--ink); margin: 0 9px; font-weight: 400; }
  .copyright { position: absolute; left: 98px; top: 63px; font-size: 12.5px; color: var(--ink); }
  .social { position: absolute; left: 926px; top: 34px; display: flex; gap: 9px; }
  .social span { width: 28px; height: 28px; border-radius: 50%; background: var(--brand-blue-dark); }
</style>
</head>
<body>
  <header class="hero" role="img" aria-label="Dusk aerial photograph of a city skyline with high-rise towers">
  </header>
  <div class="brand">BRIEFLY LEDGER</div>
  <div class="sign-in">SIGN IN</div>
  <svg class="menu-toggle" width="23" height="20" viewBox="0 0 23 20" aria-label="Menu">
    <rect x="0" y="0" width="23" height="4" fill="#fff"/>
    <rect x="0" y="8" width="23" height="4" fill="#fff"/>
    <rect x="0" y="16" width="23" height="4" fill="#fff"/>
  </svg>

  <nav class="tabs">
    <div class="tab tab--press">PRESS HEADLINES</div>
    <div class="tab tab--events">EVENTS</div>
    <div class="tab tab--briefings">BRIEFINGS</div>
  </nav>

  <section class="search-panel">
    <div class="field col-1 row-1"><label>Event Name :</label><div class="input"></div></div>
    <div class="field col-2 row-1"><label>Status :</label><div class="input"></div></div>
    <div class="field col-1 row-2"><label>Event Type :</label><div class="input"></div></div>
    <div class="field col-2 row-2"><label>Address :</label><div class="input"></div></div>
    <div class="field col-1 row-3"><label>Event Date range :</label>
      <div class="input">Past 24 hours
        <svg class="caret" width="10" height="6" viewBox="0 0 10 6"><path d="M0 0h10L5 6z" fill="#555"/></svg>
      </div>
    </div>
    <div class="field col-2 row-3"><label>Country :</label>
      <div class="input">All
        <svg class="caret" width="10" height="6" viewBox="0 0 10 6"><path d="M0 0h10L5 6z" fill="#555"/></svg>
      </div>
    </div>
    <div class="submit">SUBMIT</div>
  </section>

  <footer class="site-footer">
    <div class="footer-nav">ABOUT US<span class="sep">/</span>PRESS<span class="sep">/</span>CONTACT US</div>
    <div class="copyright">2016 © Copyrights BRIEFLY ledger.All Rights Reserved</div>
    <div class="social" aria-label="Social links">
      <span></span><span></span><span></span><span></span><span></span>
    </div>
  </footer>
</body>
</html>
```